Business Cards for company that supports physicians that do medical research

Need to create a business card for Qorvel Studies (www.qorvelstudies.example), a company devoted to supporting physicians who conduct medical research. The form of the card should match the message of research and information quest. I have provided the logo of the company as an uploaded file. Designs should be simple and slick aimed at very high end clients.

Target Market(s)

Medical doctors that are also researchers

Industry/Entity Type

Medical

Contact Information for Business Card

Should feature logo and fields for personal info:
Name/title
Phone /email

Font styles to use
Serif
Sans Serif

Requirements
Must have
• Qorvel logo and fields for personal info:
• Name: Bertrand Okonfu
• Title: VP Research and Senior Analyst
• Phone: 555-203-4719
• email: info@qorvelstudies.example
Nice to have
• Interesting cards that I've seen:
• 1- all black/charcoal or very dark background
• 2- Plastic - semi-transparent
• 3- non-standard height-width ratios
• 4- Functional cards -- USB drive incorporated
Should not have
• Too busy; needs to stay very simple

```html
<!DOCTYPE html>
<html lang="en">
<head>
<meta charset="utf-8">
<title>Qorvel Studies — Business Card</title>
<link rel="stylesheet" href="https://fonts.googleapis.com/css2?family=Open+Sans:ital,wght@0,400;0,600;0,700;1,400&display=swap">
<style>
  :root {
    --backdrop: #3a3a3a;
    --card-white: #f7f7f7;
    --brand-blue: #1b7bbd;
    --brand-green: #48b244;
    --text-light: #ffffff;
  }
  * { margin: 0; padding: 0; box-sizing: border-box; }
  html, body { width: 1200px; height: 750px; overflow: hidden; }
  body {
    background: var(--backdrop);
    font-family: "Open Sans", Arial, sans-serif;
    position: relative;
  }
  .card {
    position: absolute;
    top: 228px;
    width: 461px;
    height: 262px;
    overflow: hidden;
  }
  .card--front { left: 124px; background: var(--card-white); }
  .card--back { left: 618px; background: var(--brand-green); }

  .card__shape { position: absolute; inset: 0; }

  .brand-name {
    position: absolute;
    font-weight: 600;
    line-height: 1;
    white-space: nowrap;
  }
  .card--front .brand-name {
    left: 48px;
    top: 72px;
    font-size: 31px;
    color: var(--brand-blue);
  }
  .card--back .brand-name {
    left: 0; right: 0;
    top: 108px;
    text-align: center;
    font-size: 34px;
    color: var(--text-light);
  }

  .contact {
    position: absolute;
    right: 22px;
    top: 146px;
    text-align: right;
    color: var(--text-light);
  }
  .contact__name { font-size: 16px; font-weight: 600; line-height: 22px; }
  .contact__title { font-size: 12px; line-height: 18px; margin-bottom: 6px; }
  .contact__line {
    display: flex;
    justify-content: flex-end;
    align-items: center;
    gap: 7px;
    font-size: 11px;
    line-height: 18px;
  }
  .contact__icon { width: 12px; height: 12px; flex: none; }

  .back-web {
    position: absolute;
    left: 0; right: 0;
    top: 216px;
    text-align: center;
    color: var(--text-light);
    font-size: 11px;
    font-style: italic;
    letter-spacing: 3px;
  }
</style>
</head>
<body>

<section class="card card--front">
  <svg class="card__shape" viewBox="0 0 461 262" aria-hidden="true">
    <path d="M0,182 C60,217 180,226 280,176 C360,136 402,60 434,0 L461,0 L461,262 L0,262 Z" fill="var(--brand-blue)"/>
    <path d="M0,178 C60,214 180,222 278,172 C350,135 385,85 408,48" fill="none" stroke="var(--brand-green)" stroke-width="4" stroke-linecap="round"/>
  </svg>

  <div class="brand-name">Qorvel Studies</div>

  <div class="contact">
    <div class="contact__name">Bertrand Okonfu</div>
    <div class="contact__title">VP Research &amp; Senior Analyst</div>
    <div class="contact__line">
      <span>555-203-4719</span>
      <svg class="contact__icon" viewBox="0 0 24 24" aria-hidden="true"><path fill="#fff" d="M6.6 10.8a15 15 0 0 0 6.6 6.6l2.2-2.2a1 1 0 0 1 1-.25 11.4 11.4 0 0 0 3.6.57 1 1 0 0 1 1 1V20a1 1 0 0 1-1 1A17 17 0 0 1 3 4a1 1 0 0 1 1-1h3.5a1 1 0 0 1 1 1c0 1.25.2 2.45.57 3.57a1 1 0 0 1-.25 1z"/></svg>
    </div>
    <div class="contact__line">
      <span>info@qorvelstudies.example</span>
      <svg class="contact__icon" viewBox="0 0 24 24" aria-hidden="true"><rect x="2" y="5" width="20" height="14" rx="1" fill="#fff"/><path d="M2.5 5.5 12 13l9.5-7.5" fill="none" stroke="var(--brand-blue)" stroke-width="1.6"/></svg>
    </div>
    <div class="contact__line">
      <span>www.qorvelstudies.example</span>
      <svg class="contact__icon" viewBox="0 0 24 24" aria-hidden="true"><circle cx="12" cy="12" r="10" fill="#fff"/><path d="M2 12h20M12 2c3 3 3 17 0 20M12 2c-3 3-3 17 0 20" fill="none" stroke="var(--brand-blue)" stroke-width="1.5"/></svg>
    </div>
  </div>
</section>

<section class="card card--back">
  <div class="brand-name">Qorvel Studies</div>
  <div class="back-web">www.qorvelstudies.example</div>
</section>

</body>
</html>
```